Wine label for premium wine of vinery Mirelovac.

Design Premium wine label.

The brand is called Telvora. Brand can be extended to Ambero Telvora. There
The label should be unique and high class feeling.
This is facebook lonk of the winery
https://www.sociloop.net/402918375510264/

On facebook you can see some examole of labels that are used now. Winery is called Mirelovac, so they used letter "M" as a logo in different ways
Updates

Need extra days to review

Target Market(s)

Premium high class yet modern living traditional but also gadget fun.
I have uploaded few inspirational photos that the owner of the vinery likes. Hope it helps.

Industry/Entity Type

Vinery

Requirements
Must have
• Black, gold, silver color to be dominated. Colors that are NOT acceptable are: green, yellow, blue, purple, pink.

The name of the vinary is Mirelovac and it should be on the front label.
Nice to have
• The size of label should fit the Sorbelo application screenshot frame.
Should not have
• Cheap perception of the label and brand

```html
<!DOCTYPE html>
<html lang="en">
<head>
<meta charset="utf-8">
<title>Telvora – Cabernet Sauvignon Label</title>
<link rel="stylesheet" href="https://fonts.googleapis.com/css2?family=Cinzel:wght@500&family=Montserrat:wght@400;500;600&display=swap">
<style>
  :root {
    --backdrop: #3a3d3f;
    --label-black: #1f2021;
    --label-edge: #161717;
    --silver: #cfd2d4;
    --silver-soft: #a7abae;
    --band-silver: #7f878b;
    --band-light: #9aa2a6;
    --band-dark: #6a7275;
    --band-text: #2b2e30;
    --hill-top: #3b3d3f;
    --hill-mid: #2a2b2d;
    --hill-low: #1c1d1e;
    --crest: #8d9295;
  }
  * { margin: 0; padding: 0; box-sizing: border-box; }
  html, body {
    width: 1200px;
    height: 1018px;
    overflow: hidden;
    background: var(--backdrop);
  }
  .canvas {
    position: relative;
    width: 1200px;
    height: 1018px;
    background: linear-gradient(90deg, #333639 0%, #3c3f41 55%, #3a3d3f 100%);
  }
  .wine-label {
    position: absolute;
    left: 350px;
    top: 143px;
    width: 446px;
    height: 793px;
    background: linear-gradient(90deg, var(--label-edge) 0%, var(--label-black) 14%, #252627 50%, var(--label-black) 88%, var(--label-edge) 100%);
    overflow: hidden;
  }
  .corner-square {
    position: absolute;
    left: 423px;
    top: 3px;
    width: 12px;
    height: 12px;
    background: #878c8f;
    border: 1.5px solid var(--silver);
  }
  .brand-name {
    position: absolute;
    left: 58px;
    top: 106px;
    font-family: "Cinzel", serif;
    font-weight: 500;
    font-size: 56px;
    line-height: 1;
    letter-spacing: 3px;
    color: var(--silver);
    text-shadow: 0 1px 0 #75797c, 0 -1px 0 #0c0c0c;
  }
  .varietal {
    position: absolute;
    right: 15px;
    top: 283px;
    text-align: right;
    font-family: "Montserrat", sans-serif;
    font-weight: 500;
    font-size: 18px;
    line-height: 26px;
    color: var(--silver);
  }
  .vintage {
    position: absolute;
    right: 12px;
    top: 360px;
    font-family: "Montserrat", sans-serif;
    font-size: 12px;
    letter-spacing: 5px;
    color: var(--silver-soft);
  }
  .hill-field {
    position: absolute;
    left: 0;
    top: 378px;
    width: 446px;
    height: 382px;
  }
  .winery-band {
    position: absolute;
    left: 0;
    right: 0;
    bottom: 0;
    height: 33px;
    background: linear-gradient(180deg, var(--band-light) 0%, var(--band-silver) 45%, var(--band-dark) 100%);
    display: flex;
    align-items: center;
    justify-content: center;
  }
  .winery-name {
    font-family: "Montserrat", sans-serif;
    font-weight: 600;
    font-size: 12px;
    letter-spacing: 2.5px;
    color: var(--band-text);
  }
</style>
</head>
<body>
<main class="canvas">
  <section class="wine-label">
    <div class="corner-square"></div>
    <h1 class="brand-name">TELVORA</h1>

    <p class="varietal">CABERNET<br>SAUVIGNON</p>
    <p class="vintage">2018</p>

    <svg class="hill-field" viewBox="0 0 446 382" preserveAspectRatio="none" role="img" aria-label="Embossed flowing line pattern suggesting rolling vineyard hills">
      <defs>
        <linearGradient id="hillTone" x1="0" y1="0" x2="0" y2="1">
          <stop offset="0" stop-color="var(--hill-top)"/>
          <stop offset="0.45" stop-color="var(--hill-mid)"/>
          <stop offset="1" stop-color="var(--hill-low)"/>
        </linearGradient>
        <radialGradient id="hillSheen" cx="0.7" cy="0.35" r="0.6">
          <stop offset="0" stop-color="#4a4d50" stop-opacity="0.55"/>
          <stop offset="1" stop-color="#4a4d50" stop-opacity="0"/>
        </radialGradient>
      </defs>
      <path d="M0 150 C 40 140, 80 120, 120 112 C 180 98, 220 70, 280 45 C 340 22, 400 10, 446 6 L 446 382 L 0 382 Z" fill="url(#hillTone)"/>
      <path d="M0 150 C 40 140, 80 120, 120 112 C 180 98, 220 70, 280 45 C 340 22, 400 10, 446 6 L 446 382 L 0 382 Z" fill="url(#hillSheen)"/>
      <path d="M0 150 C 40 140, 80 120, 120 112 C 180 98, 220 70, 280 45 C 340 22, 400 10, 446 6" fill="none" stroke="var(--crest)" stroke-width="1" opacity="0.6"/>
    </svg>

    <footer class="winery-band">
      <span class="winery-name">VINARIJA MIRELOVAC</span>
    </footer>
  </section>
</main>
</body>
</html>
```